BRELWINCare.co.uk - Mental Health Clinic for Child and Adolescents

Updated 29/01/2018***
I am not sure you guys are getting the idea regards to the opening page / homescreen layout. Can you look at the new images I have uploaded (page 5, 6 and 7) These are some of the layouts I like but to incorporate my chosen images, with the BRELWIN commissioner, buttons and a sliding header bar.
I have written a strong brief, I am looking for a website, preferably wordpress as i know they are easy to maintain. I am looking for a one page site, with the top / opening page being full screen image with drop down categories. I have made a rough design, see full brief in word doc attached, there is some freedom to play around with the design aspect but it will need to relay all the content provided. I like a minimal feel. I have also attached some images that may be useful, but will need a new logo for BRELWIN Care. I have attached some logo idea's, it is up to you decide whether you want to use them.
I would prefer the homepage as full screen image, and the categories offered as a drop down or over the main image.
I have also attached linked to some competitors websites:
https://www.vorimant-health.co.uk/
http://www.qlbn.org.uk/
Industry/Entity Type
Clinic
Number of Pages Required
1 page
Font styles to use
Look and feel
Each slider illustrates characteristics of the customer's brand and the style your logo design should communicate.

```html
<!DOCTYPE html>
<html lang="en">
<head>
<meta charset="utf-8">
<title>BRELWIN Care – Child &amp; Adolescent Mental Health Services</title>
<link rel="stylesheet" href="https://fonts.googleapis.com/css2?family=Lato:wght@400;700;900&display=swap">
<style>
:root{
  --teal:#1ca3bf;
  --teal-band:rgba(28,163,191,.85);
  --pink:#e5097f;
  --purple:#6b1f78;
  --purple-dark:#4d1257;
  --green:#8cc63f;
  --green-light:#a8d240;
  --blue-dark:#1d3c8c;
  --blue-light:#17a9c6;
  --ink:#333333;
  --text:#555555;
  --white:#ffffff;
  --footer:#5e1a6c;
}
*{box-sizing:border-box;margin:0;padding:0}
html,body{width:1200px;height:2765px;overflow:hidden}
body{position:relative;font-family:'Lato',sans-serif;background:var(--white);color:var(--ink)}
a{color:inherit;text-decoration:none}

/* header */
.site-header{position:absolute;left:0;top:0;width:1200px;height:114px;background:var(--white)}
.brand{position:absolute;left:114px;top:24px;display:flex;align-items:center;gap:14px}
.brand-dot{width:62px;height:62px;border-radius:50%;background:#f4d21f}
.brand-name{font-weight:900;font-size:32px;color:var(--teal);line-height:1}
.brand-sub{font-size:11px;color:var(--ink);margin-top:4px;line-height:1.2}
.main-nav{position:absolute;left:367px;top:44px;display:flex;gap:20px;font-size:15px;font-weight:700;color:#222}
.main-nav .active{color:var(--teal)}

/* hero */
.hero{position:absolute;left:0;top:114px;width:1200px;height:572px;
  background:linear-gradient(120deg,#d8cfc4 0%,#efe9e2 45%,#c9c3bd 100%)}
.hero-pill{position:absolute;top:188px;width:276px;height:96px;border-radius:50%;
  border:4px solid var(--white);display:flex;align-items:center;justify-content:center;
  color:var(--white);font-size:24px;font-weight:700;box-shadow:0 0 0 6px rgba(0,0,0,.08)}
.hero-pill.parents{left:291px;background:var(--purple)}
.hero-pill.commissioners{left:625px;background:var(--green)}
.hero-caption{position:absolute;left:0;bottom:0;width:1200px;height:78px;background:var(--teal-band)}
.hero-caption p{position:absolute;left:124px;top:23px;color:var(--white);font-size:24px;font-weight:700}
.hero-arrows{position:absolute;right:116px;top:24px;display:flex;gap:20px}

/* welcome */
.welcome{position:absolute;left:160px;top:750px;width:885px;height:273px;border:2px solid var(--pink);border-radius:74px}
.welcome-mark{position:absolute;left:407px;top:-40px;width:72px;height:72px;border-radius:50%;background:var(--white);display:flex;align-items:center;justify-content:center}
.welcome-mark span{width:50px;height:50px;border-radius:50%;background:#f4d21f}
.welcome h1{position:absolute;top:48px;width:100%;text-align:center;font-size:34px;font-weight:700;color:#444}
.welcome h1 span{color:var(--teal)}
.welcome p{position:absolute;left:60px;top:104px;width:765px;text-align:center;font-size:19px;line-height:31px;color:var(--text)}
.btn-pink{position:absolute;left:356px;top:243px;width:172px;height:48px;border-radius:24px;background:var(--pink);color:var(--white);font-size:18px;font-weight:700;display:flex;align-items:center;justify-content:center}

/* audience split */
.audience{position:absolute;top:1098px;height:356px;color:var(--white);text-align:center}
.audience.parents{left:0;width:614px;background:linear-gradient(135deg,#8a2d8e 0%,var(--purple-dark) 100%)}
.audience.commissioners{left:614px;width:586px;background:linear-gradient(135deg,var(--green-light) 0%,#7fb923 100%)}
.audience svg{position:absolute;left:50%;top:42px;transform:translateX(-50%)}
.audience h2{position:absolute;top:127px;width:100%;font-size:26px;font-weight:700}
.audience p{position:absolute;left:50%;transform:translateX(-50%);top:164px;width:400px;font-size:15px;line-height:21px}
.btn-outline{position:absolute;left:50%;transform:translateX(-50%);width:155px;height:46px;border:2px solid var(--white);border-radius:23px;display:flex;align-items:center;justify-content:center;font-size:16px;font-weight:700;color:var(--white)}
.audience .btn-outline{top:267px}

/* blogs */
.blogs{position:absolute;left:0;top:1454px;width:1200px;height:505px;background:linear-gradient(90deg,var(--blue-dark) 0%,var(--blue-light) 100%);color:var(--white)}
.blogs h2{position:absolute;top:44px;width:100%;text-align:center;font-size:33px;font-weight:700}
.blog-card{position:absolute;top:104px;width:320px;text-align:center}
.blog-photo{width:202px;height:202px;margin:0 auto;border-radius:50%;border:5px solid #f2e600;background:linear-gradient(160deg,#d9d2cc,#8c8682)}
.blog-card h3{margin-top:16px;font-size:22px;font-weight:700}
.blog-card p{margin:4px auto 0;width:290px;font-size:15px;line-height:22px}
.blog-card .btn-outline{position:relative;left:auto;transform:none;margin:18px auto 0;width:153px;height:44px}
.blog-arrow{position:absolute;top:252px}

/* contact */
.contact{position:absolute;left:0;top:1959px;width:1200px;height:608px;background:linear-gradient(180deg,#f1f1ef 0%,#e4e3e0 100%)}
.contact-people{position:absolute;left:0;bottom:0;width:1200px;height:300px;background:linear-gradient(180deg,#c8b7a6 0%,#7d8f8f 70%,#4f7a7d 100%)}
.contact-frame{position:absolute;left:273px;top:74px;width:658px;height:340px;border:2px solid var(--pink);border-bottom:none;border-radius:60px 60px 0 0}
.contact h2{position:absolute;top:55px;width:100%;text-align:center;font-size:33px;font-weight:700;color:var(--pink)}
.contact h2 span{background:#f0f0ee;padding:0 14px}
.contact-details{position:absolute;top:115px;width:100%;text-align:center;font-size:18px;line-height:31px;color:#222}
.feedback{position:absolute;left:350px;top:253px;width:529px;height:48px;border-radius:24px;background:var(--white);box-shadow:0 1px 4px rgba(0,0,0,.15)}
.feedback span{position:absolute;left:22px;top:14px;font-size:17px;color:#555}
.feedback b{position:absolute;right:7px;top:6px;width:120px;height:36px;border-radius:18px;background:var(--teal);color:var(--white);font-size:16px;display:flex;align-items:center;justify-content:center}

/* footer */
.site-footer{position:absolute;left:0;top:2567px;width:1200px;height:198px;background:var(--footer);color:var(--white);text-align:center}
.footer-nav{position:absolute;top:40px;width:100%;display:flex;justify-content:center;gap:20px;font-size:17px;font-weight:700}
.copyright{position:absolute;top:80px;width:100%;font-size:16px}
.social{position:absolute;top:122px;left:503px;display:flex;gap:6px}
.social span{width:44px;height:44px;border-radius:50%;border:2px solid var(--white)}
</style>
</head>
<body>

<header class="site-header">
  <div class="brand">
    <span class="brand-dot"></span>
    <div>
      <div class="brand-name">BRELWIN</div>
      <div class="brand-sub">Child &amp; Adolescent Mental<br>Health Services</div>
    </div>
  </div>
  <nav class="main-nav">
    <a class="active">ABOUT US</a><a>OUR TEAM</a><a>OUR SERVICES</a><a>BLOGS</a><a>FORUM</a><a>CONTACT US</a><a>PARENTS</a><a>COMMISIONERS</a>
  </nav>
</header>

<section class="hero" role="img" aria-label="Photo of a clinician talking with a young person at a table">
  <a class="hero-pill parents">PARENTS</a>
  <a class="hero-pill commissioners">COMMISIONERS</a>
  <div class="hero-caption">
    <p>ADHD and Austim Screening with 24 Hours</p>
    <div class="hero-arrows">
      <svg width="22" height="32" viewBox="0 0 22 32"><path d="M17 3 L5 16 L17 29" fill="none" stroke="#fff" stroke-width="4"/></svg>
      <svg width="22" height="32" viewBox="0 0 22 32"><path d="M5 3 L17 16 L5 29" fill="none" stroke="#fff" stroke-width="4"/></svg>
    </div>
  </div>
</section>

<section class="welcome">
  <div class="welcome-mark"><span></span></div>
  <h1>WELCOME TO <span>BRELWIN</span></h1>
  <p>Vivamus porttitor purus nisi eleifend libero a tempus libero lectus feugiat felis Morbi diam mauris viverra in gravida eu mattis in ante Morbi eget arcu Morbi porta libero id ullamcorper nonummy nibh ligula pulvinar metus eget consectetuer augue nisi quis lacus Ut</p>
  <a class="btn-pink">READ MORE</a>
</section>

<section class="audience parents">
  <svg width="64" height="62" viewBox="0 0 64 62" aria-hidden="true">
    <circle cx="20" cy="14" r="11" fill="#fff"/><circle cx="44" cy="14" r="11" fill="#fff"/>
    <path d="M2 60 Q2 30 20 30 Q38 30 38 60 Z" fill="#fff"/><path d="M26 60 Q26 30 44 30 Q62 30 62 60 Z" fill="#fff"/>
  </svg>
  <h2>PARENTS</h2>
  <p>Vivamus porttitor purus nisi eleifend libero a tempus libero lectus feugiat felis Morbi diam mauris viverra in gravida eu mattis in ante Morbi eget arcu Morbi porta libero id ullamcorper nonummy nibh ligula pulvina</p>
  <a class="btn-outline">READ MORE</a>
</section>

<section class="audience commissioners">
  <svg width="54" height="68" viewBox="0 0 54 68" aria-hidden="true">
    <circle cx="27" cy="18" r="15" fill="#fff"/>
    <path d="M2 66 Q2 38 27 38 Q52 38 52 66 Z" fill="#fff"/>
  </svg>
  <h2>COMMISIONERS</h2>
  <p>Vivamus porttitor purus nisi eleifend libero a tempus libero lectus feugiat felis Morbi diam mauris viverra in gravida eu mattis in ante Morbi eget arcu Morbi porta libero id ullamcorper nonummy nibh ligula pulvina</p>
  <a class="btn-outline">READ MORE</a>
</section>

<section class="blogs">
  <h2>OUR BLOGS</h2>
  <svg class="blog-arrow" style="left:120px" width="26" height="38" viewBox="0 0 26 38"><path d="M20 4 L6 19 L20 34" fill="none" stroke="#fff" stroke-width="4"/></svg>
  <article class="blog-card" style="left:131px">
    <div class="blog-photo" role="img" aria-label="Photo of a girl in conversation"></div>
    <h3>Aorta libero ullamcorper</h3>
    <p>nonummy nibh ligula pulvinar metus eget consectetuer augue nisi quis</p>
    <a class="btn-outline">READ MORE</a>
  </article>
  <article class="blog-card" style="left:445px;top:112px">
    <div class="blog-photo" role="img" aria-label="Photo of a smiling young woman"></div>
    <h3>Fusce ultricies orci</h3>
    <p>nonummy nibh ligula pulvinar metus eget consectetuer augue nisi quis</p>
    <a class="btn-outline">READ MORE</a>
  </article>
  <article class="blog-card" style="left:760px;top:112px">
    <div class="blog-photo" role="img" aria-label="Photo of a boy sitting in a classroom"></div>
    <h3>Nulla rhoncus dictu</h3>
    <p>nonummy nibh ligula pulvinar metus eget consectetuer augue nisi quis</p>
    <a class="btn-outline">READ MORE</a>
  </article>
  <svg class="blog-arrow" style="left:1069px" width="26" height="38" viewBox="0 0 26 38"><path d="M6 4 L20 19 L6 34" fill="none" stroke="#fff" stroke-width="4"/></svg>
</section>

<section class="contact" role="img" aria-label="Light brick wall background">
  <div class="contact-frame"></div>
  <div class="contact-people" role="img" aria-label="Photo of a group of smiling young people sitting on a sofa"></div>
  <h2><span>CONTACT US</span></h2>
  <div class="contact-details">
    Phone Number: 0208 555 0192<br>
    Address:&nbsp; Larchfield Suite 2B, 41-47 Mill Lane, London, E19 4RT<br>
    Opening Times: 9am – 5pm Mon-Fri<br>
    Email: enquiry@brelwincare.co.uk
  </div>
  <div class="feedback"><span>Type Feedback</span><b>SUBMIT</b></div>
</section>

<footer class="site-footer">
  <nav class="footer-nav">
    <a>ABOUT US</a><a>OUR TEAM</a><a>OUR SERVICES</a><a>BLOGS</a><a>CONTACT US</a><a>PARENTS</a><a>COMMISIONERS</a>
  </nav>
  <p class="copyright">© 2018 Company Name&nbsp; All right reserved</p>
  <div class="social" aria-label="Social links"><span></span><span></span><span></span><span></span></div>
</footer>

</body>
</html>
```